TA BRAMLEY BUSINESS CARD DESIGN PROJECT

We need to utilize our logo that was expertly created on PixelHarbor and now need to match this with a business card design.

```html
<!DOCTYPE html>
<html lang="en">
<head>
<meta charset="utf-8">
<title>TA BRAMLEY Business Card</title>
<link href="https://fonts.googleapis.com/css2?family=Montserrat:wght@400;500;800&display=swap" rel="stylesheet">
<style>
  :root {
    --brand-blue: #1452a8;
    --card-white: #ffffff;
    --ink-black: #1e1e1f;
    --text-dark: #222222;
    --backdrop: #d9d9dc;
  }
  * { margin: 0; padding: 0; box-sizing: border-box; }
  html, body {
    width: 1200px;
    height: 900px;
    overflow: hidden;
    background: var(--backdrop);
    font-family: "Montserrat", sans-serif;
  }
  .stage {
    position: relative;
    width: 1200px;
    height: 900px;
    display: flex;
    flex-direction: column;
    align-items: center;
    justify-content: center;
    gap: 50px;
  }
  .card {
    position: relative;
    width: 680px;
    height: 390px;
    background: var(--card-white);
    border-radius: 26px;
    overflow: hidden;
    box-shadow: 0 12px 30px rgba(0,0,0,0.18);
  }
  .wordmark {
    color: var(--brand-blue);
    font-weight: 800;
    letter-spacing: 0.12em;
    white-space: nowrap;
  }
  .card-front {
    display: flex;
    align-items: center;
    justify-content: center;
  }
  .card-front .wordmark { font-size: 64px; }

  .card-back .wordmark {
    position: absolute;
    top: 58px;
    right: 46px;
    font-size: 40px;
  }
  .accent-bar {
    position: absolute;
    left: 0;
    top: 132px;
    width: 18px;
    height: 56px;
    background: var(--brand-blue);
  }
  .identity {
    position: absolute;
    left: 44px;
    top: 130px;
  }
  .identity .person-name {
    color: var(--brand-blue);
    font-weight: 800;
    font-size: 27px;
    letter-spacing: 0.02em;
  }
  .identity .person-role {
    color: var(--text-dark);
    font-weight: 400;
    font-size: 19px;
    margin-top: 2px;
  }
  .wave {
    position: absolute;
    left: 0;
    top: 0;
    width: 680px;
    height: 390px;
  }
  .contact-list {
    position: absolute;
    left: 44px;
    bottom: 28px;
    list-style: none;
    color: var(--card-white);
    font-size: 17px;
    font-weight: 400;
  }
  .contact-list li {
    display: flex;
    align-items: center;
    gap: 12px;
    line-height: 30px;
  }
  .contact-list svg { width: 16px; height: 16px; fill: var(--brand-blue); flex: none; }
</style>
</head>
<body>
  <main class="stage">
    <section class="card card-front" aria-label="Card front">
      <div class="wordmark">TA BRAMLEY</div>
    </section>

    <section class="card card-back" aria-label="Card back">
      <svg class="wave" viewBox="0 0 680 390" aria-hidden="true">
        <path d="M0 390 L0 252 C150 226 320 216 460 202 C585 188 650 162 680 112 L680 390 Z" fill="var(--ink-black)"/>
        <path d="M30 243 C170 216 325 205 460 191 C585 177 645 150 672 108" fill="none" stroke="var(--brand-blue)" stroke-width="5" stroke-linecap="round"/>
      </svg>

      <div class="wordmark">TA BRAMLEY</div>

      <div class="accent-bar"></div>
      <div class="identity">
        <div class="person-name">NORA WHITCOMBE</div>
        <div class="person-role">Managing Director</div>
      </div>

      <ul class="contact-list">
        <li>
          <svg viewBox="0 0 24 24"><path d="M6.6 10.8a15.1 15.1 0 0 0 6.6 6.6l2.2-2.2a1 1 0 0 1 1-.25 11.4 11.4 0 0 0 3.6.57 1 1 0 0 1 1 1V20a1 1 0 0 1-1 1A17 17 0 0 1 3 4a1 1 0 0 1 1-1h3.5a1 1 0 0 1 1 1c0 1.25.2 2.45.57 3.6a1 1 0 0 1-.25 1z"/></svg>
          <span>123 456 789</span>
        </li>
        <li>
          <svg viewBox="0 0 24 24"><path d="M2 5h20v14H2z M2 5l10 8 10-8" /></svg>
          <span>info@yourmail.com</span>
        </li>
        <li>
          <svg viewBox="0 0 24 24"><circle cx="12" cy="12" r="10"/></svg>
          <span>www.yourwebsite.com</span>
        </li>
      </ul>
    </section>
  </main>
</body>
</html>
```